Front page of Orthodox Christian Monastery Website

I am attaching a couple of versions of design that was already created for the front page of the website. You can grab the same pictures and titles (do not need to know the Russian language) to create your own version of design.
Background: Monastery website contains sermons, stories about monastery life, monastery music of the sisterhood.
Main principles of the design:
1. Various materials/sermons/music have to be clearly visible immediately to the site visitor.
2. Text descriptions to photos should be using font with a good contrast, highly clickable and easily readable.
3. Every article should have a photo or a quality picture (use those in the sample) that will convey something about it.
4. On the top, there will be a menu, which will be a line of words (just use generic words for now).
5. Design should reflect Christian Orthodox themes and fonts.
Updates

Target Market(s)

Orthodox Christian believers around the world and those that are interested in Orthodox Christianity

Number of Pages Required

1 page

Font styles to use
Serif

Colors

Designer to choose colors to be used in the design.

Requirements
Must have
• In the project description
Nice to have
• for some ideas see a popular Orthodox Christian website:
• www.verenskaya-lampada.ru
• We don't want to copy it, but it could give ideas.
Should not have
• Should not be overly complex

```html
<!DOCTYPE html>
<html lang="en">
<head>
<meta charset="utf-8">
<title>Orthodox Christian Monastery</title>
<link rel="stylesheet" href="https://fonts.googleapis.com/css2?family=Oswald:wght@400;500;600&family=Open+Sans:wght@400;600;700&display=swap">
<style>
:root{
  --blue:#2b4fa3;
  --blue-dark:#1f3f8a;
  --ink:#1d1d1d;
  --text:#555;
  --muted:#666;
  --line:#dcdcdc;
  --page:#f2f2f2;
  --panel:#ffffff;
  --footer:#121212;
  --hero-a:#2a1810;
  --hero-b:#6e4428;
}
*{box-sizing:border-box;margin:0;padding:0}
html,body{width:1200px;height:4119px;overflow:hidden}
body{position:relative;background:var(--page);font-family:"Open Sans",Arial,sans-serif;color:var(--text)}
a{color:inherit;text-decoration:none}

/* header */
.site-header{position:absolute;left:0;top:0;width:1200px;height:104px;background:#fff}
.brand{position:absolute;left:99px;top:20px;font-family:"Oswald",Arial,sans-serif;color:var(--ink)}
.brand-name{font-size:33px;font-weight:600;line-height:38px;letter-spacing:.5px}
.brand-sub{font-size:19px;font-weight:400;letter-spacing:6px;line-height:24px}
.main-nav{position:absolute;right:99px;top:40px;display:flex;gap:30px;align-items:center;font-family:"Oswald",Arial,sans-serif;font-size:15px;font-weight:500;color:var(--ink)}
.main-nav .active{color:var(--blue)}
.main-nav svg{width:16px;height:16px}

/* hero */
.hero{position:absolute;left:0;top:104px;width:1200px;height:506px;overflow:hidden}
.hero-photo{position:absolute;inset:0;background:radial-gradient(ellipse at 50% 60%,#9a6236 0%,var(--hero-b) 30%,var(--hero-a) 80%)}
.hero-shade{position:absolute;inset:0;background:rgba(0,0,0,.25)}
.hero-content{position:absolute;left:0;width:100%;top:118px;text-align:center;color:#fff}
.hero-title{font-family:"Oswald",Arial,sans-serif;font-size:56px;font-weight:500;line-height:66px;letter-spacing:.5px}
.hero-text{font-size:24px;margin-top:20px}
.hero-btn{display:inline-block;margin-top:28px;width:184px;height:55px;line-height:51px;border:2px solid #fff;border-radius:28px;font-family:"Oswald",Arial,sans-serif;font-size:16px;letter-spacing:.5px}
.hero-dots{position:absolute;top:438px;left:0;width:100%;display:flex;justify-content:center;gap:5px}
.hero-dots span{width:11px;height:11px;border-radius:50%;border:2px solid #fff}
.hero-dots span.on{background:#fff}

/* panels */
.panel{position:absolute;background:var(--panel);border:1px solid var(--line);box-shadow:0 1px 3px rgba(0,0,0,.06)}
.panel-title{font-family:"Oswald",Arial,sans-serif;font-size:30px;font-weight:500;color:var(--ink);line-height:40px;padding-top:18px}
.content-panel{left:99px;width:659px;height:1019px;padding:0 22px 0 25px}
.panel-sermons{top:684px}
.panel-life{top:1735px}
.panel-music{top:2790px}

.tabs{display:flex;justify-content:space-between;border-top:1px solid var(--line);border-bottom:1px solid var(--line);margin-top:16px;height:66px;padding:10px 30px 0 30px}
.tab{width:90px;text-align:center;font-size:14px;color:var(--ink);font-weight:600;letter-spacing:.3px}
.tab svg{display:block;margin:0 auto 4px;width:22px;height:22px;fill:var(--blue)}

.article{display:flex;height:247px;padding-top:36px;border-bottom:1px solid var(--line)}
.article-photo{width:211px;height:192px;flex:none;border:4px solid #fff;box-shadow:0 0 0 1px #ddd}
.article-body{margin-left:41px;padding-top:10px;width:362px}
.article-title{font-family:"Oswald",Arial,sans-serif;font-size:21px;font-weight:500;color:var(--ink);line-height:30px;white-space:nowrap}
.article-rating{font-size:13px;color:var(--muted);margin-top:2px}
.article-text{font-size:13px;line-height:24px;color:var(--text);margin-top:14px}
.read-more{display:block;margin-top:16px;font-size:13px;font-weight:700;color:var(--blue);letter-spacing:.3px}

.btn{display:block;width:146px;height:47px;line-height:47px;text-align:center;background:var(--blue);color:#fff;border-radius:24px;font-family:"Oswald",Arial,sans-serif;font-size:15px;letter-spacing:.5px}
.content-panel .btn{margin-top:36px}

/* sidebar */
.side-panel{left:785px;width:316px;padding:0 22px}
.panel-media{top:684px;height:511px}
.panel-gallery{top:1225px;height:703px}
.side-panel .panel-title{border-bottom:1px solid var(--line);padding-bottom:14px}
.media-item{display:flex;height:132px;padding-top:22px;border-bottom:1px solid var(--line)}
.media-item:last-child{border-bottom:none}
.media-thumb{width:104px;height:88px;flex:none;border:3px solid #fff;box-shadow:0 0 0 1px #ddd}
.media-body{margin-left:20px}
.media-title{font-family:"Oswald",Arial,sans-serif;font-size:15px;font-weight:500;color:var(--ink);line-height:23px}
.media-author{font-size:12px;color:var(--muted);margin-top:6px}
.gallery-grid{display:grid;grid-template-columns:126px 126px;column-gap:20px;row-gap:15px;margin-top:20px}
.gallery-tile{height:114px;border:3px solid #fff;box-shadow:0 0 0 1px #ddd}
.panel-gallery .btn{margin-top:32px;margin-left:6px}

/* footer */
.site-footer{position:absolute;left:0;top:3921px;width:1200px;height:198px;background:var(--footer);color:#fff;text-align:center;font-size:13px}
.social{position:absolute;top:-29px;left:0;width:100%;display:flex;justify-content:center;gap:16px}
.social span{width:58px;height:58px;border-radius:50%;background:#fff;border:3px solid var(--footer);display:flex;align-items:center;justify-content:center}
.social svg{width:22px;height:22px;fill:var(--blue-dark)}
.footer-contacts{padding-top:72px;display:flex;justify-content:center;gap:14px;align-items:center}
.footer-contacts svg{width:12px;height:12px;fill:#fff;vertical-align:-1px;margin-right:6px}
.footer-links{margin-top:20px}
.footer-copy{margin-top:16px}
</style>
</head>
<body>
<svg width="0" height="0" style="position:absolute">
  <symbol id="i-info" viewBox="0 0 24 24"><circle cx="12" cy="12" r="11"/><rect x="10.5" y="10" width="3" height="8" fill="#fff"/><circle cx="12" cy="6.8" r="1.8" fill="#fff"/></symbol>
  <symbol id="i-book" viewBox="0 0 24 24"><path d="M6 2h14v17H7a2 2 0 0 0 0 3h13v1H7a3 3 0 0 1-3-3V4a2 2 0 0 1 2-2z"/></symbol>
  <symbol id="i-music" viewBox="0 0 24 24"><path d="M9 4l12-3v15a3 3 0 1 1-2-2.8V6L11 8v11a3 3 0 1 1-2-2.8z"/></symbol>
  <symbol id="i-heart" viewBox="0 0 24 24"><path d="M12 22S2 14.5 2 8a5 5 0 0 1 10-1 5 5 0 0 1 10 1c0 6.5-10 14-10 14z"/></symbol>
  <symbol id="i-video" viewBox="0 0 24 24"><rect x="1" y="5" width="15" height="14" rx="2"/><path d="M17 10l6-4v12l-6-4z"/></symbol>
  <symbol id="i-pin" viewBox="0 0 24 24"><path d="M12 1a8 8 0 0 1 8 8c0 6-8 14-8 14S4 15 4 9a8 8 0 0 1 8-8zm0 5a3 3 0 1 0 0 6 3 3 0 0 0 0-6z"/></symbol>
  <symbol id="i-phone" viewBox="0 0 24 24"><path d="M6 2l4 5-2 3a12 12 0 0 0 6 6l3-2 5 4-2 4C10 22 2 14 2 4z"/></symbol>
  <symbol id="i-mail" viewBox="0 0 24 24"><path d="M1 5h22v14H1z"/><path d="M1 5l11 8 11-8" fill="none" stroke="#888" stroke-width="1.5"/></symbol>
  <symbol id="i-share" viewBox="0 0 24 24"><circle cx="18" cy="5" r="3"/><circle cx="6" cy="12" r="3"/><circle cx="18" cy="19" r="3"/><path d="M8.5 10.8l7-4M8.5 13.2l7 4" stroke-width="2" fill="none" stroke="currentColor"/></symbol>
  <symbol id="i-chat" viewBox="0 0 24 24"><path d="M3 4h18v12H9l-5 4v-4H3z"/></symbol>
</svg>

<header class="site-header">
  <div class="brand">
    <div class="brand-name">ORTHODOX CHRISTIAN</div>
    <div class="brand-sub">MONASTERY</div>
  </div>
  <nav class="main-nav">
    <a class="active">HOME</a><a>ABOUT US</a><a>PHOTO GALLERY</a><a>NEWS</a><a>CALENDAR</a><a>CONTACT</a>
    <svg viewBox="0 0 24 24"><circle cx="10" cy="10" r="7" fill="none" stroke="#1d1d1d" stroke-width="3"/><path d="M15 15l7 7" stroke="#1d1d1d" stroke-width="3"/></svg>
  </nav>
</header>

<section class="hero">
  <div class="hero-photo" role="img" aria-label="Clergy in vestments holding candles during a service inside a dim stone church"></div>
  <div class="hero-shade"></div>
  <div class="hero-content">
    <h1 class="hero-title">ORTHODOX CHRISTIAN MONASTERY</h1>
    <p class="hero-text">At vero eos et accusamus et iusto odio dignissimos duc</p>
    <a class="hero-btn">GET MORE INFO</a>
  </div>
  <div class="hero-dots"><span class="on"></span><span></span><span></span><span></span></div>
</section>

<section class="panel content-panel panel-sermons">
  <h2 class="panel-title">SERMONS</h2>
  <div class="tabs">
    <div class="tab"><svg><use href="#i-info"/></svg>STORIES</div>
    <div class="tab"><svg><use href="#i-book"/></svg>BOOKS</div>
    <div class="tab"><svg><use href="#i-music"/></svg>MUSIC</div>
    <div class="tab"><svg><use href="#i-heart"/></svg>LIFESTYLE</div>
    <div class="tab"><svg><use href="#i-video"/></svg>VIDEO</div>
  </div>
  <article class="article">
    <div class="article-photo" role="img" aria-label="Icon of a saint with gold halo" style="background:linear-gradient(135deg,#3a2a14,#a8782c 55%,#2c1f10)"></div>
    <div class="article-body">
      <h3 class="article-title">Imitation of Christ</h3>
      <p class="article-rating">Rating: 9,5 | Votes: 12</p>
      <p class="article-text">In the best moments of our life, when we are inspired to live a good life, to love everyone and everything, and to do good deeds, we cannot find a more...</p>
      <a class="read-more">READ MORE</a>
    </div>
  </article>
  <article class="article">
    <div class="article-photo" role="img" aria-label="Priest in red vestments holding a book" style="background:linear-gradient(135deg,#e4d6c4,#c0302a 50%,#8a1c18)"></div>
    <div class="article-body">
      <h3 class="article-title">The Courage to Be Human</h3>
      <p class="article-rating">Rating: 9,2 | Votes: 9</p>
      <p class="article-text">Jesus asks us as he asked the paralytic 2000 years ago, do you want to be made well? Are you willing to make the spiritual changes in your life...</p>
      <a class="read-more">READ MORE</a>
    </div>
  </article>
  <article class="article">
    <div class="article-photo" role="img" aria-label="Ornate golden church interior with hanging lamps" style="background:linear-gradient(180deg,#2a1a10,#8a5a2a 60%,#3a2414)"></div>
    <div class="article-body">
      <h3 class="article-title">From Pastor to Priest</h3>
      <p class="article-rating">Rating: 9,7 | Votes: 38</p>
      <p class="article-text">In 2009, the well-known Russian Protestant pastor Pavel Lirin converted to Orthodoxy along with his entire community of neo-Pentecostals.</p>
      <a class="read-more">READ MORE</a>
    </div>
  </article>
  <a class="btn">VIEW MORE</a>
</section>

<section class="panel content-panel panel-life">
  <h2 class="panel-title">MONASTERY LIFE</h2>
  <div class="tabs">
    <div class="tab"><svg><use href="#i-info"/></svg>STORIES</div>
    <div class="tab"><svg><use href="#i-book"/></svg>BOOKS</div>
    <div class="tab"><svg><use href="#i-music"/></svg>MUSIC</div>
    <div class="tab"><svg><use href="#i-heart"/></svg>LIFESTYLE</div>
    <div class="tab"><svg><use href="#i-video"/></svg>VIDEO</div>
  </div>
  <article class="article">
    <div class="article-photo" role="img" aria-label="Monk holding a lit candle in darkness" style="background:radial-gradient(circle at 50% 35%,#b07a3a,#3a2414 45%,#120a06)"></div>
    <div class="article-body">
      <h3 class="article-title">The House of Mercy</h3>
      <p class="article-rating">Rating: 9,6 | Votes: 14</p>
      <p class="article-text">Today's reading paints a vivid picture of pain and suffering and the hope of healing. We hear about a place in Jerusalem with a miraculous</p>
      <a class="read-more">READ MORE</a>
    </div>
  </article>
  <article class="article">
    <div class="article-photo" role="img" aria-label="Priests in green vestments serving at the altar" style="background:linear-gradient(135deg,#4a5a3a,#8a9a6a 50%,#3a3024)"></div>
    <div class="article-body">
      <h3 class="article-title">The Empty Tomb(s)</h3>
      <p class="article-rating">Rating: 7,4 | Votes: 12</p>
      <p class="article-text">We have to make our churches full of God's grace by becoming a living temple because we each are alive in Christ. Then people will not come...</p>
      <a class="read-more">READ MORE</a>
    </div>
  </article>
  <article class="article">
    <div class="article-photo" role="img" aria-label="Church interior lit by rows of candles" style="background:linear-gradient(180deg,#6a5a4a,#2a2018 60%,#4a3a28)"></div>
    <div class="article-body">
      <h3 class="article-title">Glistening with splendor!</h3>
      <p class="article-rating">Rating: 10 | Votes: 5</p>
      <p class="article-text">Today finds us at the exact midpoint of the sacred 50-day period between the Feasts of Pascha and Pentecost. So, this 25th day is called...</p>
      <a class="read-more">READ MORE</a>
    </div>
  </article>
  <a class="btn">VIEW MORE</a>
</section>

<section class="panel content-panel panel-music">
  <h2 class="panel-title">MONASTERY MUSIC OF THE SISTERHOOD</h2>
  <div class="tabs">
    <div class="tab"><svg><use href="#i-info"/></svg>STORIES</div>
    <div class="tab"><svg><use href="#i-book"/></svg>BOOKS</div>
    <div class="tab"><svg><use href="#i-music"/></svg>MUSIC</div>
    <div class="tab"><svg><use href="#i-heart"/></svg>LIFESTYLE</div>
    <div class="tab"><svg><use href="#i-video"/></svg>VIDEO</div>
  </div>
  <article class="article">
    <div class="article-photo" role="img" aria-label="Colourful painted icon of the Mother of God" style="background:linear-gradient(135deg,#2a6a7a,#c8a040 50%,#8a2a3a)"></div>
    <div class="article-body">
      <h3 class="article-title">The Mother of God Ran Us Through a Sieve</h3>
      <p class="article-rating">Rating: 9,6 | Votes: 27</p>
      <p class="article-text">When I went to the monastery, I thought I was ready for monastic life: sewing, knitting, cooking... Only years later did I realize that I don't know how...</p>
      <a class="read-more">READ MORE</a>
    </div>
  </article>
  <article class="article">
    <div class="article-photo" role="img" aria-label="Monk reading by candlelight" style="background:radial-gradient(circle at 40% 40%,#8a6a4a,#2a1c12 55%,#0e0a08)"></div>
    <div class="article-body">
      <h3 class="article-title">The Church in Seventh Century Celtic..</h3>
      <p class="article-rating">Rating: 9,4 | Votes: 21</p>
      <p class="article-text">In the seventh century A.D., the population of Britain consisted mainly of two ethnic groups relatively equal in number, collectively known as the Celts...</p>
      <a class="read-more">READ MORE</a>
    </div>
  </article>
  <article class="article">
    <div class="article-photo" role="img" aria-label="Baptism of a child in a church" style="background:linear-gradient(135deg,#5a3a22,#b07040 50%,#3a2416)"></div>
    <div class="article-body">
      <h3 class="article-title">Take Them In for Heaven's Sake!</h3>
      <p class="article-rating">Rating: 10 | Votes: 19</p>
      <p class="article-text">Fr. Simon baptizes and integrates children into Church life, and Marina teaches and comforts them. And the adolescents who once lived in an atmosphere...</p>
      <a class="read-more">READ MORE</a>
    </div>
  </article>
  <a class="btn">VIEW MORE</a>
</section>

<aside class="panel side-panel panel-media">
  <h2 class="panel-title">MEDIA REVIEW</h2>
  <div class="media-item">
    <div class="media-thumb" role="img" aria-label="Open old book with a candle" style="background:linear-gradient(135deg,#3a2a1a,#8a6a4a)"></div>
    <div class="media-body">
      <h3 class="media-title">With the Faith of Angels a Church is Built</h3>
      <p class="media-author">Fr. Peter Alden</p>
    </div>
  </div>
  <div class="media-item">
    <div class="media-thumb" role="img" aria-label="Church dome under a blue sky" style="background:linear-gradient(180deg,#2a5aa8,#8ab0d8 60%,#d8d0c0)"></div>
    <div class="media-body">
      <h3 class="media-title">BREAKING: Timothy Hale has died</h3>
      <p class="media-author">Mark &amp; Helen Varga</p>
    </div>
  </div>
  <div class="media-item">
    <div class="media-thumb" role="img" aria-label="Archaeological excavation site" style="background:linear-gradient(135deg,#6a6a6a,#b0a898 60%,#4a4a4a)"></div>
    <div class="media-body">
      <h3 class="media-title">Excavations start on Palestine's oldest...</h3>
      <p class="media-author">Mira Haddad</p>
    </div>
  </div>
</aside>

<aside class="panel side-panel panel-gallery">
  <h2 class="panel-title">PHOTO GALLERY</h2>
  <div class="gallery-grid">
    <div class="gallery-tile" role="img" aria-label="Sheet music on a piano" style="background:linear-gradient(135deg,#1a1a1a,#8a8a8a)"></div>
    <div class="gallery-tile" role="img" aria-label="Crowd at an outdoor procession" style="background:linear-gradient(135deg,#3a3a3a,#7a7060)"></div>
    <div class="gallery-tile" role="img" aria-label="Candles glowing in a dark church" style="background:radial-gradient(circle,#c07a30,#2a1408 70%)"></div>
    <div class="gallery-tile" role="img" aria-label="Faithful holding candles at night" style="background:radial-gradient(circle,#a86a30,#1e1008 70%)"></div>
    <div class="gallery-tile" role="img" aria-label="Hand lighting a candle" style="background:linear-gradient(135deg,#8a2a2a,#d8a0a0 50%,#3a1a1a)"></div>
    <div class="gallery-tile" role="img" aria-label="White monastery walls with green trees" style="background:linear-gradient(135deg,#d8d8d0,#6a8a4a 60%,#5a3a2a)"></div>
    <div class="gallery-tile" role="img" aria-label="Clergy procession in white vestments" style="background:linear-gradient(135deg,#e0dcd4,#8a7a6a)"></div>
    <div class="gallery-tile" role="img" aria-label="Colourful church banners" style="background:linear-gradient(135deg,#c83a3a,#d8a040 50%,#3a6a8a)"></div>
  </div>
  <a class="btn">VIEW MORE</a>
</aside>

<footer class="site-footer">
  <div class="social">
    <span aria-label="Share"><svg style="color:#1f3f8a"><use href="#i-share"/></svg></span>
    <span aria-label="Message"><svg><use href="#i-chat"/></svg></span>
    <span aria-label="Call"><svg><use href="#i-phone"/></svg></span>
    <span aria-label="Email"><svg viewBox="0 0 24 24"><path d="M2 5h20v14H2z"/><path d="M2 5l10 8 10-8" fill="none" stroke="#fff" stroke-width="1.6"/></svg></span>
  </div>
  <div class="footer-contacts">
    <span><svg><use href="#i-pin"/></svg>Nam libero tempor &nbsp;soluta nobis est</span><span>|</span>
    <span><svg><use href="#i-phone"/></svg>1 888 888 8888</span><span>|</span>
    <span><svg><use href="#i-mail"/></svg>info@monasterylife.org</span>
  </div>
  <div class="footer-links">Help &nbsp;| &nbsp;FAQ &nbsp;| &nbsp;Support &nbsp;| &nbsp;Sitemap &nbsp;| &nbsp;Terms Of Use &nbsp;| &nbsp;Privacy Statement</div>
  <div class="footer-copy">Copyrights © 2018, Orthodox Christian Monastery,. All rights reserved.</div>
</footer>
</body>
</html>
```